Lanternfield Drinks business cards

We need a business card design for our new logo. The company is modern, progressive, professional, yet approachable. The key products are ready to drink bottles and cans of coffee based beverages.
These cards will be a critical part of the first impression made by our sales organization, business development team, and all external facing personnel.
Card can be a vertical or horizontal orientation.

Target Market(s)

Customers, suppliers, business partners

Industry/Entity Type

Business

Contact Information for Business Card

Business cards should feature Company Name and Logo.

Font styles to use
Serif

Colors

Designer to choose colors to be used in the design.

Requirements
Must have
• Strong readability of Name, phone #, mobile number and email address.
• Job title, website url, Street Address, and other details can be secondary level readability.
Nice to have
• High impact, simplistic quality design.
• Ok to utilize the 'H in the box' separate from the company name

```html
<!DOCTYPE html>
<html lang="en">
<head>
<meta charset="utf-8">
<title>Lanternfield Drinks – Business Card</title>
<link rel="stylesheet" href="https://fonts.googleapis.com/css2?family=Crimson+Pro:wght@400;600&display=swap">
<style>
  :root {
    --page-bg: #e6e2dd;
    --orange-deep: #c85a1f;
    --orange-light: #e98a3e;
    --frost: #eeefef;
    --frost-shade: #d9dbdc;
    --edge-dark: #2a1d16;
    --brand-orange: #d0552a;
    --brand-gold: #c79a3b;
    --text-light: #fbeee3;
  }
  * { margin: 0; padding: 0; box-sizing: border-box; }
  html, body {
    width: 1200px; height: 1054px; overflow: hidden;
    background: var(--page-bg);
    font-family: "Crimson Pro", Georgia, serif;
  }
  .card {
    position: absolute; left: 100px; top: 224px;
    width: 1000px; height: 606px;
    border-radius: 6px; overflow: hidden;
    box-shadow: 0 10px 30px rgba(0,0,0,.18);
  }
  .card-art { position: absolute; inset: 0; }
  .holder { position: absolute; left: 57px; color: var(--text-light); }
  .holder-name { top: 44px; font-size: 34px; font-weight: 600; }
  .holder-title { top: 94px; font-size: 23px; font-weight: 400; }
  .contact-list { position: absolute; left: 62px; top: 352px; list-style: none; color: var(--text-light); }
  .contact-list li {
    display: flex; align-items: center; height: 34px;
    font-size: 25px; letter-spacing: .2px;
  }
  .contact-list svg { width: 22px; height: 22px; margin-right: 22px; fill: var(--text-light); }
  .address {
    position: absolute; left: 57px; top: 510px;
    font-size: 24px; color: rgba(251,238,227,.75);
  }
  .brand-mark {
    position: absolute; left: 712px; top: 244px;
    width: 114px; height: 114px;
    border: 5px solid var(--brand-orange);
  }
  .brand-block {
    position: absolute; left: 872px; top: 303px;
    transform: translate(-50%, -50%) rotate(-90deg);
    display: flex; flex-direction: column; align-items: center;
  }
  .brand-rule { width: 400px; height: 2px; background: var(--brand-gold); }
  .brand-name {
    padding: 6px 0;
    font-size: 36px; font-weight: 600; letter-spacing: 2px;
    color: var(--brand-orange); white-space: nowrap;
  }
</style>
</head>
<body>
  <div class="card">
    <svg class="card-art" viewBox="0 0 1000 606" preserveAspectRatio="none" aria-hidden="true">
      <defs>
        <linearGradient id="orangeFill" x1="0" y1="0" x2="1" y2="1">
          <stop offset="0" stop-color="var(--orange-light)"/>
          <stop offset="1" stop-color="var(--orange-deep)"/>
        </linearGradient>
        <linearGradient id="frostFill" x1="0" y1="0" x2="1" y2="0">
          <stop offset="0" stop-color="var(--frost-shade)"/>
          <stop offset="1" stop-color="var(--frost)"/>
        </linearGradient>
      </defs>
      <rect width="1000" height="606" fill="url(#frostFill)"/>
      <path d="M700 0 Q592 303 692 606 H672 Q576 303 700 0 Z" fill="var(--edge-dark)"/>
      <path d="M0 0 H700 Q578 303 672 606 H0 Z" fill="url(#orangeFill)"/>
    </svg>

    <div class="holder holder-name">John Doe Smith</div>
    <div class="holder holder-title">Managing Director</div>

    <ul class="contact-list">
      <li>
        <svg viewBox="0 0 24 24" aria-hidden="true"><path d="M3 8c0-3 4-4 9-4s9 1 9 4v2h-5V8H8v2H3z M6 12h12l2 8H4z M12 14a2.5 2.5 0 1 0 0 5a2.5 2.5 0 1 0 0-5z"/></svg>
        555.555.5555
      </li>
      <li>
        <svg viewBox="0 0 24 24" aria-hidden="true"><path d="M7 2h10a2 2 0 0 1 2 2v16a2 2 0 0 1-2 2H7a2 2 0 0 1-2-2V4a2 2 0 0 1 2-2zm0 3v12h10V5zm5 14a1 1 0 1 0 0 2a1 1 0 1 0 0-2z"/></svg>
        666.666.7777
      </li>
      <li>
        <svg viewBox="0 0 24 24" aria-hidden="true"><path d="M2 5h20v14H2z M3.5 6.5 12 13l8.5-6.5" stroke="var(--orange-deep)" stroke-width="1.4"/></svg>
        johndoe@yourwebsite.com
      </li>
      <li>
        <svg viewBox="0 0 24 24" aria-hidden="true"><path d="M12 2a10 10 0 1 0 0 20a10 10 0 1 0 0-20zm0 1.8c-1.5 2-2.3 4.6-2.4 7.2h4.8c-.1-2.6-.9-5.2-2.4-7.2zM4 11h4c.1-2.3.7-4.5 1.7-6.4A8.2 8.2 0 0 0 4 11zm12 0h4a8.2 8.2 0 0 0-5.7-6.4c1 1.9 1.6 4.1 1.7 6.4zM4 13a8.2 8.2 0 0 0 5.7 6.4c-1-1.9-1.6-4.1-1.7-6.4zm5.6 0c.1 2.6.9 5.2 2.4 7.2c1.5-2 2.3-4.6 2.4-7.2zm6.4 0c-.1 2.3-.7 4.5-1.7 6.4A8.2 8.2 0 0 0 20 13z"/></svg>
        www.yourwebsite.com
      </li>
    </ul>

    <div class="address">234 Anywhere St., Any Town, US 123456</div>

    <div class="brand-mark" aria-hidden="true"></div>
    <div class="brand-block">
      <div class="brand-rule"></div>
      <div class="brand-name">LANTERNFIELD DRINKS CO</div>
      <div class="brand-rule"></div>
    </div>
  </div>
</body>
</html>
```